Qorlant Business Card

We require a stunning business card for Qorlant - a new digital marketing agency. The logo provided was designed by a graphic designer here on Pixelfair.

www.qorlant.example - "Get more sales online"

What we do:
The business delivers website optimisation (Web design, social media strategy, digital strategies, SEO, PPC, conversion optimisation, email marketing) to get businesses more sales online.

The card must match the brand style which can be found on this website template:

http://layoutbazaar.example/item/gridmark-sharp-adaptive-allpurpose-theme/full_screen_preview/7301926

It must have 'wow' factor so that you'll never forget Qorlant - We're open to any materials, textures you think will work.

We don't want a boring run of the mill design - I can knock that up in Photoshop myself or use a template solution. It should be timeless and only need replacing should the contact details change.

The design should be eye catching, future proof, exceptionally chic, classy and oozing authority and confidence. Qorlant services must not look cheap.

Here's some brilliant designs to point you in the right direction:

http://tidyworks.example/30-remarkable-calling-cards/

The spec is for double sided, but we're open to your ideas. If it's going on an opaque or see through card, then of course a single side is preferable. Using creativity and thought on the medium for the card - shape - texture is desirable.

The strapline for the business is "Get more business online" please submit with / without strapline.
Updates

Please only submit your best 1-3 designs initially.

Target Market(s)

Business 2 Business - Local SMEs
Local professionals - Doctors, Dentists, Financials, Bespoke Retailers, Property companies - anyone with a decent budget to spend on digital marketing services and a high margin product or service to sell.

Industry/Entity Type

Graphic Designer

Requirements
Must have
• Text:
• name: Tom Calwayne
• position Digital Marketing Director
• mobile 07912 403 615
• website www.qorlant.example
Nice to have
• Check See http://tidyworks.example/30-remarkable-calling-cards/ for ideas.
• LinkedIn and Twitter usernames if there is space and it works on the design.

```html
<!DOCTYPE html>
<html lang="en">
<head>
<meta charset="utf-8">
<title>Qorlant Business Card</title>
<link rel="stylesheet" href="https://fonts.googleapis.com/css2?family=Didact+Gothic&family=Open+Sans:wght@400;600&display=swap">
<style>
  :root {
    --stage: #1c1c1e;
    --card: #26272a;
    --card-edge: #2e2f33;
    --brand-red: #e8402a;
    --brand-teal: #1e5564;
    --text-light: #e6e6e6;
    --text-muted: #b9b9bd;
  }
  * { margin: 0; padding: 0; box-sizing: border-box; }
  html, body {
    width: 1200px; height: 900px; overflow: hidden;
    background: var(--stage);
  }
  .stage {
    position: relative; width: 1200px; height: 900px;
    background: radial-gradient(ellipse at 55% 40%, #2a2a2d 0%, var(--stage) 70%);
  }
  .card {
    position: absolute; top: 300px; width: 520px; height: 300px;
    background: var(--card);
    border: 1px solid var(--card-edge);
    box-shadow: 0 18px 40px rgba(0,0,0,.6);
    overflow: hidden;
  }
  .card--front { left: 50px; }
  .card--back { left: 630px; }

  .wordmark {
    display: flex; align-items: center; gap: 10px;
    font-family: "Didact Gothic", sans-serif;
    color: var(--brand-red);
    line-height: 1;
  }
  .wordmark__dot {
    border-radius: 50%; background: var(--brand-red); flex: none;
  }
  .card--front .wordmark { position: absolute; left: 70px; top: 92px; font-size: 76px; }
  .card--front .wordmark__dot { width: 40px; height: 40px; }
  .card--front .tagline {
    position: absolute; left: 74px; top: 186px;
    font-family: "Didact Gothic", sans-serif; font-size: 17px;
    color: var(--text-light); font-weight: 600; letter-spacing: .2px;
  }

  .card--back .wordmark { position: absolute; left: 28px; top: 26px; font-size: 40px; gap: 8px; }
  .card--back .wordmark__dot { width: 22px; height: 22px; }
  .card--back .tagline {
    position: absolute; left: 32px; top: 76px;
    font-family: "Didact Gothic", sans-serif; font-size: 10.5px;
    color: var(--text-light);
  }
  .rule {
    position: absolute; left: 0; right: 0; height: 1px;
    background: var(--brand-teal);
  }
  .rule--top { top: 70px; }
  .rule--name { top: 200px; left: 300px; }

  .contacts {
    position: absolute; left: 30px; top: 118px; list-style: none;
    font-family: "Open Sans", sans-serif; font-size: 10px; color: var(--text-muted);
  }
  .contacts li { margin-bottom: 8px; }
  .contacts .label { color: var(--brand-teal); display: inline-block; width: 12px; font-weight: 600; }

  .person { position: absolute; left: 320px; top: 166px; font-family: "Open Sans", sans-serif; }
  .person__name { font-size: 16px; color: var(--brand-red); }
  .person__role { font-size: 8px; color: var(--brand-teal); margin-top: 2px; }

  .address {
    position: absolute; left: 320px; top: 236px;
    font-family: "Open Sans", sans-serif; font-size: 10.5px; line-height: 1.35;
    color: var(--text-muted);
  }
</style>
</head>
<body>
<main class="stage">
  <section class="card card--front" aria-label="Card front">
    <div class="wordmark"><span class="wordmark__dot"></span><span>Qorlant</span></div>
    <p class="tagline">Clear presence on the web for growing companies</p>
  </section>

  <section class="card card--back" aria-label="Card back">
    <div class="wordmark"><span class="wordmark__dot"></span><span>Qorlant</span></div>
    <div class="rule rule--top"></div>
    <p class="tagline">Clear presence on the web for growing companies</p>

    <ul class="contacts">
      <li><span class="label">T</span> 555-555-5555</li>
      <li><span class="label">M</span> 555-555-5555</li>
      <li><span class="label">E</span> info@qorlant.example</li>
      <li><span class="label">W</span> www.qorlant.example</li>
    </ul>

    <div class="person">
      <p class="person__name">Employee name</p>
      <p class="person__role">CEO</p>
    </div>
    <div class="rule rule--name"></div>

    <p class="address">Street name, city name,<br>zip code with country</p>
  </section>
</main>
</body>
</html>
```